Dietitian needs awesome business card

I need a contemporary design that's eye catching but professional.
My card is to given to doctors, specialists and patients alike.
I manage patients with chronic diseases
I have uploaded my logo and current business card, I would also like the other Certified Clinical Nutritionist logo incorporated into the design

Target Market(s)

Doctors, specialists and patients

Industry/Entity Type

Healthcare

Contact Information for Business Card

www.brightfieldnutrition.com.au
Ph: 0427 561 903
Fax: 6457 2183
email: marcus.k.diet@fernmail.com
Space on the back of the card with: Appointment date, Appointment time and appointment location

Font styles to use
Serif

Colors
fbee3e
876aae
ffc214

Requirements
Must have
• My Logo
• Certified Clinical Nutritionist Logo
• My 4 locations - Pinebrook Medical Centre, North Corrin Health, Hollis Medical, Ashcombe Doctors Surgery
Nice to have
• I like the colours in my current business card

```html
<!DOCTYPE html>
<html lang="en">
<head>
<meta charset="utf-8">
<title>Brightfield Nutrition &amp; Dietetics – Business Card</title>
<link rel="stylesheet" href="https://fonts.googleapis.com/css2?family=Open+Sans:wght@400;600;700&display=swap">
<style>
  :root {
    --navy: #1a2a8c;
    --blue: #1f5fb8;
    --green: #7dc21e;
    --green-deep: #2e9a3a;
    --orange: #f26b1d;
    --grey: #4a4a4a;
    --rule: #c9cdd2;
    --page: #e9eaec;
    --card: #ffffff;
  }
  * { margin: 0; padding: 0; box-sizing: border-box; }
  html, body { width: 1200px; height: 987px; overflow: hidden; }
  body {
    background: var(--page);
    font-family: "Open Sans", Arial, sans-serif;
    position: relative;
  }
  .card {
    position: absolute;
    left: 293px;
    width: 615px;
    height: 351px;
    background: var(--card);
    border-radius: 22px;
    overflow: hidden;
    box-shadow: 0 2px 6px rgba(0,0,0,.18);
  }
  .card--front { top: 128px; }
  .card--back { top: 507px; }

  /* Front */
  .brand {
    position: absolute; left: 40px; top: 58px;
    display: flex; align-items: center; gap: 12px;
  }
  .brand__dot {
    width: 44px; height: 44px; border-radius: 50%;
    background: var(--blue);
  }
  .brand__name { font-size: 20px; font-weight: 400; color: var(--navy); white-space: nowrap; }
  .person { position: absolute; left: 40px; top: 140px; }
  .person__name { font-size: 22px; font-weight: 600; color: var(--navy); line-height: 28px; }
  .person__role { font-size: 16.5px; line-height: 23px; }
  .person__role--primary { color: var(--orange); }
  .person__role--secondary { color: var(--green); }
  .contacts { position: absolute; left: 40px; top: 222px; list-style: none; }
  .contacts li {
    display: flex; align-items: center; gap: 12px;
    font-size: 16.5px; color: var(--grey); height: 23.5px; white-space: nowrap;
  }
  .contacts svg { width: 16px; height: 16px; fill: var(--navy); flex: none; }
  .swoosh { position: absolute; right: 0; top: 0; width: 615px; height: 351px; }

  /* Back */
  .photo-wash {
    position: absolute; inset: 0;
    background: linear-gradient(120deg, #eef3ea 0%, #f7f9f5 35%, #eef2ea 60%, #fafbf9 100%);
  }
  .appointment__title {
    position: absolute; left: 0; right: 0; top: 28px;
    text-align: center; font-size: 20px; font-weight: 600; color: var(--navy);
  }
  .appointment__line {
    position: absolute; left: 42px; width: 531px; height: 1px; background: var(--rule);
  }
  .when {
    position: absolute; left: 42px; top: 220px; width: 531px; height: 24px;
    font-size: 16px; color: var(--navy); white-space: nowrap;
  }
  .when > span { position: absolute; top: 0; line-height: 24px; }
  .when__label--date { left: 0; }
  .when__dots { overflow: hidden; font-size: 13px; letter-spacing: 0.5px; }
  .when__dots--date { left: 56px; width: 222px; }
  .when__label--time { left: 285px; }
  .when__dots--time { left: 338px; width: 140px; }
  .when__ampm { left: 484px; font-size: 12.5px; }
  .locations {
    position: absolute; left: 42px; top: 263px; width: 540px;
    display: grid; grid-template-columns: 306px 1fr; row-gap: 2px; list-style: none;
  }
  .locations li {
    display: flex; align-items: center; gap: 6px; white-space: nowrap;
    font-size: 16.5px; color: var(--grey); line-height: 22px;
  }
  .locations .box {
    width: 14px; height: 14px; border: 1.5px solid var(--navy); flex: none;
  }
</style>
</head>
<body>

<section class="card card--front">
  <div class="brand">
    <span class="brand__dot"></span>
    <span class="brand__name">Brightfield Nutrition &amp; Dietetics</span>
  </div>

  <div class="person">
    <p class="person__name">Marcus Kellaway</p>
    <p class="person__role person__role--primary">Certified Clinical Nutritionist</p>
    <p class="person__role person__role--secondary">Nutritionist &amp; Chef</p>
  </div>

  <ul class="contacts">
    <li><svg viewBox="0 0 16 16"><path d="M3.5 1l2.5 3-1.5 2c.8 2 2.6 3.8 4.5 4.5l2-1.5 3 2.5-1.5 2.5C7 14 2 9 1 2.5z"/></svg>0427 561 903</li>
    <li><svg viewBox="0 0 16 16"><path d="M4 1h8v4H4zM1 6h14v6h-3v3H4v-3H1zM5 10v4h6v-4z"/></svg>6457 2183</li>
    <li><svg viewBox="0 0 16 16"><path d="M1 3h14v10H1z"/><path d="M2.5 4.5 8 9l5.5-4.5" fill="none" stroke="#fff" stroke-width="1.2"/></svg>marcus.k.diet@fernmail.com</li>
    <li><svg viewBox="0 0 16 16"><circle cx="8" cy="8" r="7"/><path d="M4 5c2 0 3 1 2 3s1 3 0 5M10 2c-1 2 1 3 3 3M11 9c1 1 0 3 1 4" fill="none" stroke="#fff" stroke-width="1.3"/></svg>brightfieldnutrition.com.au</li>
  </ul>

  <svg class="swoosh" viewBox="0 0 615 351" aria-hidden="true">
    <defs>
      <linearGradient id="blueSweep" x1="0" y1="0" x2="0" y2="1">
        <stop offset="0" stop-color="#1a8fd6"/>
        <stop offset="1" stop-color="#141f86"/>
      </linearGradient>
      <linearGradient id="greenSweep" x1="0" y1="0" x2="0" y2="1">
        <stop offset="0" stop-color="#c4e02a"/>
        <stop offset="1" stop-color="#1f9a3a"/>
      </linearGradient>
    </defs>
    <path d="M608 30 C600 170 540 290 478 351 L615 351 L615 30 Z" fill="url(#greenSweep)"/>
    <path d="M611 45 C604 180 548 295 489 351 L615 351 L615 45 Z" fill="#fff"/>
    <path d="M614 55 C608 190 555 300 497 351 L615 351 Z" fill="url(#blueSweep)"/>
  </svg>
</section>

<section class="card card--back">
  <div class="photo-wash" role="img" aria-label="Soft faded photograph of fresh vegetables and herbs"></div>
  <h2 class="appointment__title">YOUR APPOINTMENT</h2>
  <div class="appointment__line" style="top:83px"></div>
  <div class="appointment__line" style="top:118px"></div>
  <div class="appointment__line" style="top:153px"></div>
  <div class="appointment__line" style="top:188px"></div>

  <div class="when">
    <span class="when__label--date">Date :</span>
    <span class="when__dots when__dots--date">....................................................................</span>
    <span class="when__label--time">Time :</span>
    <span class="when__dots when__dots--time">............................................</span>
    <span class="when__ampm">AM/PM</span>
  </div>

  <ul class="locations">
    <li><span class="box"></span>Pinebrook Medical Centre</li>
    <li><span class="box"></span>Hollis Medical</li>
    <li><span class="box"></span>North Corrin Health</li>
    <li><span class="box"></span>Ashcombe Doctors Surgery</li>
  </ul>
</section>

</body>
</html>
```